Business card for law firm

Need business card for new law firm. Think confident, authoritative, conservative, but not stuffy or old-fashioned.

Contact Information for Business Card

Content for card - logo (uploaded), plus the following:

Paul Whitcombe (larger font)
Managing Partner (larger font, but not as large as name)
Level 9, 7 Ferris Lane
Sydney NSW 2000
Main Tel 02 9364 2710
Direct Tel 02 8472 3159
Email paul@qvlegal.com.au
www.qvlegal.com.au

Letterhead design should include logo plus:
Level 9, 7 Ferris Lane
Sydney NSW 2000
Tel 02 8472 3159
www.qvlegal.com.au

```html
<!DOCTYPE html>
<html lang="en">
<head>
<meta charset="utf-8">
<title>Quayview Legal – Business Card</title>
<link rel="stylesheet" href="https://fonts.googleapis.com/css2?family=Open+Sans:wght@400;600;700&display=swap">
<style>
  :root {
    --navy: #15225e;
    --ink: #3a3a3a;
    --muted: #555555;
    --rule: #c9c9c9;
    --paper: #ffffff;
    --backdrop: #e7e4e1;
  }
  * { box-sizing: border-box; margin: 0; padding: 0; }
  html, body {
    width: 1200px; height: 997px; overflow: hidden;
    background: var(--backdrop);
    font-family: "Open Sans", Arial, sans-serif;
  }
  .sheet {
    width: 1200px; height: 997px;
    display: flex; align-items: center; justify-content: center; gap: 48px;
  }
  .card {
    position: relative;
    width: 520px; height: 300px;
    background: var(--paper);
    box-shadow: 0 2px 6px rgba(0,0,0,0.12);
    overflow: hidden;
  }
  .brand {
    display: flex; align-items: center; gap: 12px;
    color: var(--navy);
  }
  .brand-mark {
    width: 30px; height: 30px; background: var(--navy);
  }
  .brand-name {
    font-weight: 600; font-size: 23px; letter-spacing: 0.06em;
    text-transform: uppercase; white-space: nowrap;
  }
  /* front */
  .card-front .brand {
    position: absolute; left: 40px; top: 118px;
  }
  .card-front .brand-name { font-size: 19px; }
  .divider {
    position: absolute; left: 262px; top: 36px;
    width: 1px; height: 190px; background: var(--rule);
  }
  .contact {
    position: absolute; left: 284px; top: 40px;
    color: var(--ink); font-size: 11px; line-height: 1.45;
  }
  .contact-name {
    color: var(--navy); font-weight: 700; font-size: 15px;
    text-transform: uppercase; letter-spacing: 0.01em;
  }
  .contact-role { font-size: 12px; color: var(--muted); margin-bottom: 8px; }
  .contact-address { margin-bottom: 8px; }
  .contact-line { display: flex; align-items: center; gap: 6px; }
  .contact-line svg { width: 10px; height: 10px; fill: var(--navy); flex: none; }
  .band { position: absolute; left: 0; bottom: 0; width: 520px; height: 80px; }
  .band-url {
    position: absolute; right: 26px; bottom: 11px;
    color: #fff; font-size: 12px; letter-spacing: 0.06em;
  }
  /* back */
  .card-back { display: flex; align-items: center; justify-content: center; }
  .card-back .brand-name { font-size: 24px; }
</style>
</head>
<body>
<main class="sheet">
  <section class="card card-front" aria-label="Card front">
    <div class="brand">
      <span class="brand-mark"></span>
      <span class="brand-name">Quayview Legal</span>
    </div>
    <div class="divider"></div>
    <div class="contact">
      <p class="contact-name">Paul Whitcombe</p>
      <p class="contact-role">Managing Partner</p>
      <p class="contact-address">Level 9, 7 Ferris Lane<br>Sydney NSW 2000</p>
      <p class="contact-line">
        <svg viewBox="0 0 10 10"><path d="M2 0.5 L3.6 2.6 L2.7 3.7 Q3.8 5.9 6.3 7.3 L7.4 6.4 L9.5 8 L8.4 9.5 Q4.6 9.3 0.5 1.6 Z"/></svg>
        02 9364 2710 (Main)
      </p>
      <p class="contact-line">
        <svg viewBox="0 0 10 10"><path d="M2 0.5 L3.6 2.6 L2.7 3.7 Q3.8 5.9 6.3 7.3 L7.4 6.4 L9.5 8 L8.4 9.5 Q4.6 9.3 0.5 1.6 Z"/></svg>
        02 8472 3159 (Direct)
      </p>
      <p class="contact-line">
        <svg viewBox="0 0 10 10"><path d="M0.5 2 H9.5 V8.5 H0.5 Z M1 2.4 L5 5.6 L9 2.4" fill="none" stroke="#15225e" stroke-width="1.1"/></svg>
        paul@qvlegal.com.au
      </p>
    </div>
    <svg class="band" viewBox="0 0 520 80" aria-hidden="true">
      <path d="M230 80 Q238 46 272 44 L520 30 V80 Z" fill="#15225e"/>
      <path d="M272 41 L520 26" stroke="#15225e" stroke-width="1.5" fill="none"/>
    </svg>
    <span class="band-url">www.qvlegal.com.au</span>
  </section>

  <section class="card card-back" aria-label="Card back">
    <div class="brand">
      <span class="brand-mark"></span>
      <span class="brand-name">Quayview Legal</span>
    </div>
  </section>
</main>
</body>
</html>
```